Coastline Premier Retreats Business Card Design

Design a business card for Coastline Premier Retreats. Look at the website for colors and reference. Card should have logo, name, title, office number, mobile number, email, URL and a tagline like, "Luxury Hotel & Resort Email Marketing" (This might change).

https://www.coastlinepremierretreats.example

The rest I will leave up to your imagination.

Contact Information for Business Card

Logo, name, title, office number, mobile number, email, URL and a tagline like, "Luxury Hotel & Resort Email Marketing" (This might change).

```html
<!DOCTYPE html>
<html lang="en">
<head>
<meta charset="utf-8">
<title>Coastline Premier Retreats — Business Card</title>
<link rel="stylesheet" href="https://fonts.googleapis.com/css2?family=Open+Sans:wght@400;600;700&display=swap">
<style>
  :root {
    --stage: #232323;
    --card: #1f1f23;
    --accent: #f26f1d;
    --ink: #ffffff;
    --rule: #8a8a8e;
    --font: "Open Sans", Arial, sans-serif;
  }
  * { box-sizing: border-box; margin: 0; padding: 0; }
  html, body { width: 1200px; height: 780px; overflow: hidden; }
  body {
    background: var(--stage);
    font-family: var(--font);
    color: var(--ink);
    position: relative;
  }
  .card {
    position: absolute;
    width: 520px;
    height: 300px;
    background: var(--card);
    box-shadow: 0 14px 30px rgba(0,0,0,.55);
  }
  .card--front { left: 50px; top: 240px; }
  .card--back  { left: 630px; top: 240px; }

  .wordmark {
    display: flex;
    align-items: center;
    gap: 12px;
    font-weight: 600;
    color: var(--ink);
    white-space: nowrap;
  }
  .wordmark__mark { background: var(--accent); flex: none; }

  .card--front .wordmark {
    position: absolute; inset: 0;
    justify-content: center;
    font-size: 30px;
  }
  .card--front .wordmark__mark { width: 18px; height: 18px; }

  .card--back .wordmark {
    position: absolute; left: 22px; top: 132px;
    font-size: 15.5px; gap: 8px;
  }
  .card--back .wordmark__mark { width: 10px; height: 10px; }

  .divider {
    position: absolute; left: 262px; top: 48px;
    width: 1px; height: 170px; background: var(--rule);
  }

  .person { position: absolute; left: 282px; top: 52px; }
  .person__name { font-size: 22px; font-weight: 700; line-height: 1.1; }
  .person__first { color: var(--accent); }
  .person__title { font-size: 13px; font-weight: 600; margin-top: 3px; }

  .contacts {
    position: absolute; left: 282px; top: 118px;
    list-style: none;
    font-size: 10.5px; line-height: 1;
  }
  .contacts li { display: flex; align-items: center; gap: 7px; height: 20px; }
  .contacts svg { width: 12px; height: 12px; flex: none; fill: none; stroke: var(--accent); stroke-width: 1.6; stroke-linecap: round; stroke-linejoin: round; }

  .tagline {
    position: absolute; left: 0; right: 0; bottom: 34px;
    padding-left: 170px;
    color: var(--accent);
    font-size: 14px;
    text-align: center;
  }
</style>
</head>
<body>

  <section class="card card--front" aria-label="Business card front">
    <div class="wordmark"><span class="wordmark__mark"></span>Coastline Premier Retreats</div>
  </section>

  <section class="card card--back" aria-label="Business card back">
    <div class="wordmark"><span class="wordmark__mark"></span>Coastline Premier Retreats</div>
    <div class="divider"></div>

    <div class="person">
      <p class="person__name"><span class="person__first">Marta</span> Vellinger</p>
      <p class="person__title">Co-Founder</p>
    </div>

    <ul class="contacts">
      <li>
        <svg viewBox="0 0 24 24"><path d="M5 3h4l2 5-3 2a12 12 0 0 0 6 6l2-3 5 2v4a2 2 0 0 1-2 2A18 18 0 0 1 3 5a2 2 0 0 1 2-2z"/></svg>
        (555) 014-2758
      </li>
      <li>
        <svg viewBox="0 0 24 24"><rect x="6" y="2" width="12" height="20" rx="2"/><path d="M11 18h2"/></svg>
        (555) 014-7777
      </li>
      <li>
        <svg viewBox="0 0 24 24"><circle cx="12" cy="12" r="10"/><path d="M2 12h20M12 2a15 15 0 0 1 0 20M12 2a15 15 0 0 0 0 20"/></svg>
        www.coastlinepremierretreats.example
      </li>
      <li>
        <svg viewBox="0 0 24 24"><rect x="2" y="5" width="20" height="14" rx="1"/><path d="M2 6l10 7 10-7"/></svg>
        info@coastlinepremierretreats.example
      </li>
    </ul>

    <p class="tagline">Luxury Hotel &amp; Resort Email Marketing</p>
  </section>

</body>
</html>
```